Accountancy firm needs clean and simple website and optional logo

We need a logo and basic wordpress website design for a Sydney based accountancy firm.
We need a clean and simple logo and website, based on the accounting/finance/tax industry. Simple, credible and official colors.
The logo is expected to be so simple that we have combined into the one job.
If you submit a logo design and we choose it along with someone else's website design you will be paid a bonus of $60. The website design will still win the competition as per normal.
Current website is old and terrible but gives you an idea of the sitemap (super simple) and what they do: www.brookfiscal.com.au
We want original different to normal template looking designs.
We like videos, and like http://www.merivane.com.au/
Feel free to go to clipvault9 and use some videos from there.
We are based in Sydney Australia and in the field of taxation and accounting
We want a clean, formal, credible site, limited pages.
The project is guaranteed, so go for it.
Logo Text
Brook & Associates

```html
<!DOCTYPE html>
<html lang="en">
<head>
<meta charset="utf-8">
<title>Brook &amp; Associates</title>
<link rel="stylesheet" href="https://fonts.googleapis.com/css2?family=Montserrat:wght@400;500;600;700&display=swap">
<style>
  :root {
    --navy-deep: #0a2a52;
    --navy-mid: #1f5d96;
    --brand-blue: #1aa3ee;
    --white: #ffffff;
    --ink: #2a2a2a;
    --muted: #8a8a8a;
    --light-band: #f2f2f2;
    --grey-band: #dcdcdc;
    --call-band: #3a3a3a;
    --footer: #2b2b2b;
    --field: rgba(255,255,255,0.55);
  }
  * { box-sizing: border-box; margin: 0; padding: 0; }
  html, body { width: 1200px; height: 3140px; overflow: hidden; }
  body { font-family: "Montserrat", Arial, sans-serif; color: var(--ink); background: var(--white); position: relative; }
  section, header, footer { position: absolute; left: 0; width: 1200px; }
  .abs { position: absolute; }
  .center { left: 0; width: 1200px; text-align: center; }

  /* Hero */
  .hero { top: 0; height: 690px; overflow: hidden; }
  .hero-photo { position: absolute; inset: 0;
    background: radial-gradient(ellipse at 70% 40%, #3f8ccc 0%, var(--navy-mid) 35%, var(--navy-deep) 80%); }
  .wordmark { color: var(--white); font-weight: 600; font-size: 16px; letter-spacing: 0.3px; white-space: nowrap; }
  .site-logo { left: 85px; top: 64px; }
  .main-nav { left: 0; top: 64px; }
  .main-nav a { position: absolute; color: var(--white); text-decoration: none; font-size: 17px; font-weight: 500; white-space: nowrap; }
  .hero-title { top: 255px; color: var(--white); font-weight: 600; font-size: 70px; line-height: 62px; letter-spacing: 1px; }
  .hero-lead { top: 390px; color: var(--white); font-size: 15px; }
  .hero-button { top: 425px; left: 490px; width: 220px; height: 40px; border-radius: 20px;
    background: linear-gradient(#ffffff, #d8d8d8); color: #555; font-size: 19px; line-height: 40px; text-align: center; }
  .slider-dots { top: 597px; left: 578px; display: flex; gap: 6px; }
  .slider-dots span { width: 13px; height: 13px; border-radius: 50%; border: 2px solid var(--white); }
  .slider-dots span.active { background: var(--white); }

  /* Intro */
  .intro { top: 690px; height: 505px; background: var(--white); }
  .section-title { font-weight: 600; text-transform: uppercase; color: var(--ink); }
  .section-sub { color: var(--muted); font-size: 12px; }
  .intro .section-title { top: 110px; font-size: 23px; }
  .intro .section-sub { top: 140px; }
  .feature { top: 222px; width: 220px; text-align: center; }
  .feature h3 { font-size: 17px; font-weight: 500; text-transform: uppercase; margin-bottom: 10px; }
  .feature p { font-size: 11.5px; line-height: 17px; color: var(--muted); }

  /* Services & values */
  .services { top: 1195px; height: 473px; background: var(--light-band); }
  .values { top: 1668px; height: 532px; background: var(--grey-band); }
  .services .section-title { top: 100px; font-size: 31px; }
  .services .section-sub { top: 142px; font-size: 14px; }
  .values .section-title { top: 118px; font-size: 31px; }
  .values .section-sub { top: 160px; font-size: 14px; }
  .card { width: 250px; text-align: center; }
  .card h4 { font-size: 13px; font-weight: 600; text-transform: uppercase; margin: 14px 0 8px; }
  .card p { font-size: 11px; line-height: 16px; color: var(--muted); }
  .tile-icon { width: 62px; height: 62px; margin: 0 auto; display: block; }
  .ring-icon { width: 88px; height: 88px; margin: 0 auto; display: block; }
  .ring-line { top: 277px; left: 370px; width: 460px; height: 2px; background: #9a9a9a; }

  /* Call */
  .call { top: 2200px; height: 280px; background: var(--call-band); color: var(--white); }
  .call-badge { top: -42px; left: 555px; width: 90px; height: 90px; }
  .call-label { top: 112px; font-size: 30px; font-weight: 500; }
  .call-number { top: 170px; font-size: 44px; font-weight: 400; letter-spacing: 1px; }

  /* Contact */
  .contact { top: 2480px; height: 530px; overflow: hidden; }
  .contact-photo { position: absolute; inset: 0;
    background: linear-gradient(160deg, #c9d8e8 0%, #8fa9c6 45%, #4d6f9a 100%); }
  .contact .section-title { top: 72px; font-size: 24px; color: var(--white); font-weight: 500; }
  .contact .section-sub { top: 100px; color: #e6eef6; font-size: 11px; }
  .field { left: 333px; width: 530px; background: var(--field); border: 1px solid rgba(255,255,255,0.7); }
  .field-name { top: 145px; height: 47px; }
  .field-email { top: 203px; height: 48px; }
  .field-message { top: 263px; height: 137px; }
  .send-button { top: 432px; left: 510px; width: 180px; height: 33px; border-radius: 17px;
    background: linear-gradient(#ffffff, #d6d6d6); color: #444; font-size: 14px; font-weight: 500; line-height: 33px; text-align: center; }

  /* Footer */
  .site-footer { top: 3010px; height: 130px; background: var(--footer); }
  .footer-logo { left: 140px; top: 56px; font-size: 15px; }
  .social { top: 48px; width: 42px; height: 42px; border-radius: 50%; background: var(--white); }
</style>
</head>
<body>

<header class="hero">
  <div class="hero-photo" role="img" aria-label="Photo of glowing blue stock market charts and candlestick graphs"></div>
  <div class="wordmark site-logo abs">Brook &amp; Associates</div>
  <nav class="main-nav abs center">
    <a style="left:702px">HOME</a>
    <a style="left:808px">ABOUT</a>
    <a style="left:932px">BLOG</a>
    <a style="left:1028px">CONTACT</a>
  </nav>
  <h1 class="hero-title abs center">LOREM IPSUM<br>DOLOR</h1>
  <p class="hero-lead abs center">Proin iaculis purus consequat sem cure.</p>
  <div class="hero-button abs">Proin iaculis</div>
  <div class="slider-dots abs"><span class="active"></span><span></span><span></span></div>
</header>

<section class="intro">
  <h2 class="section-title abs center">Suspendisse Potenti</h2>
  <p class="section-sub abs center">Lorem ipsum dolor sit amet</p>
  <div class="feature abs" style="left:142px">
    <h3>Praesent Varius</h3>
    <p>Lorem ipsum dolor sit amet consectetur adipiscing elit. Morbi vel elementum augue. In hac habitasse platea dictumst. Sed ullamcorper ante quam, eu fringilla est elementum sit amet. Vestibulum non ligula neque.</p>
  </div>
  <div class="feature abs" style="left:372px">
    <h3>Donec</h3>
    <p>Lorem ipsum dolor sit amet consectetur adipiscing elit. Morbi vel elementum augue. In hac habitasse platea dictumst. Sed ullamcorper ante quam, eu fringilla est elementum sit amet. Vestibulum non ligula neque.</p>
  </div>
  <div class="feature abs" style="left:605px">
    <h3>Sed Pretium</h3>
    <p>Lorem ipsum dolor sit amet consectetur adipiscing elit. Morbi vel elementum augue. In hac habitasse platea dictumst. Sed ullamcorper ante quam, eu fringilla est elementum sit amet. Vestibulum non ligula neque.</p>
  </div>
  <div class="feature abs" style="left:840px">
    <h3>Integer a Ante</h3>
    <p>Lorem ipsum dolor sit amet consectetur adipiscing elit. Morbi vel elementum augue. In hac habitasse platea dictumst. Sed ullamcorper ante quam, eu fringilla est elementum sit amet. Vestibulum non ligula neque.</p>
  </div>
</section>

<section class="services">
  <h2 class="section-title abs center">Professional Services</h2>
  <p class="section-sub abs center">Proin iaculis purus consequat sem cure</p>
  <div class="card abs" style="left:202px;top:210px">
    <svg class="tile-icon" viewBox="0 0 62 62" aria-hidden="true">
      <rect width="62" height="62" rx="6" fill="#1aa3ee"/>
      <rect x="14" y="14" width="34" height="34" rx="3" fill="none" stroke="#fff" stroke-width="2.5"/>
      <line x1="14" y1="22" x2="48" y2="22" stroke="#fff" stroke-width="2.5"/>
      <g fill="#fff"><rect x="18" y="26" width="5" height="5"/><rect x="28" y="26" width="5" height="5"/><rect x="38" y="26" width="5" height="5"/><rect x="18" y="34" width="5" height="5"/><rect x="28" y="34" width="5" height="5"/><rect x="38" y="34" width="5" height="5"/><rect x="18" y="41" width="5" height="4"/><rect x="28" y="41" width="5" height="4"/></g>
    </svg>
    <h4>Beautiful Designs</h4>
    <p>Proin iaculis purus consequat sem cure digni ssim. Donec porttitora entum suscipit aenean rhoncus posuere nibh in tincidunt.</p>
  </div>
  <div class="card abs" style="left:475px;top:210px">
    <svg class="tile-icon" viewBox="0 0 62 62" aria-hidden="true">
      <rect width="62" height="62" rx="6" fill="#1aa3ee"/>
      <rect x="15" y="12" width="32" height="38" rx="3" fill="none" stroke="#fff" stroke-width="2.5"/>
      <g stroke="#fff" stroke-width="2.5"><line x1="20" y1="21" x2="42" y2="21"/><line x1="20" y1="28" x2="42" y2="28"/><line x1="20" y1="35" x2="42" y2="35"/><line x1="20" y1="42" x2="42" y2="42"/></g>
    </svg>
    <h4>Responsive Web</h4>
    <p>Proin iaculis purus consequat sem cure digni ssim. Donec porttitora entum suscipit aenean rhoncus posuere nibh in tincidunt.</p>
  </div>
  <div class="card abs" style="left:748px;top:210px">
    <svg class="tile-icon" viewBox="0 0 62 62" aria-hidden="true">
      <rect width="62" height="62" rx="6" fill="#1aa3ee"/>
      <rect x="13" y="13" width="36" height="36" fill="#fff"/>
      <polyline points="16,42 25,31 32,36 45,20" fill="none" stroke="#1aa3ee" stroke-width="3"/>
      <polygon points="45,17 47,25 40,21" fill="#1aa3ee"/>
    </svg>
    <h4>Marketing Tools</h4>
    <p>Proin iaculis purus consequat sem cure digni ssim. Donec porttitora entum suscipit aenean rhoncus posuere nibh in tincidunt.</p>
  </div>
</section>

<section class="values">
  <h2 class="section-title abs center">Culture &amp; Values</h2>
  <p class="section-sub abs center">Proin iaculis purus consequat sem cure</p>
  <div class="ring-line abs"></div>
  <div class="card abs" style="left:202px;top:234px">
    <svg class="ring-icon" viewBox="0 0 88 88" aria-hidden="true">
      <circle cx="44" cy="44" r="41" fill="#fff" stroke="#6d6d6d" stroke-width="5"/>
      <rect x="31" y="28" width="26" height="32" rx="3" fill="none" stroke="#6d6d6d" stroke-width="2.5"/>
      <rect x="35" y="32" width="18" height="6" fill="#6d6d6d"/>
      <g fill="#6d6d6d"><rect x="35" y="42" width="4" height="4"/><rect x="42" y="42" width="4" height="4"/><rect x="49" y="42" width="4" height="4"/><rect x="35" y="50" width="4" height="4"/><rect x="42" y="50" width="4" height="4"/><rect x="49" y="50" width="4" height="4"/></g>
    </svg>
    <h4>Work-Life Balance</h4>
    <p>Proin iaculis purus consequat sem cure digni ssim. Donec porttitora entum suscipit aenean rhoncus posuere nibh in tincidunt.</p>
  </div>
  <div class="card abs" style="left:475px;top:234px">
    <svg class="ring-icon" viewBox="0 0 88 88" aria-hidden="true">
      <circle cx="44" cy="44" r="41" fill="#fff" stroke="#6d6d6d" stroke-width="5"/>
      <rect x="29" y="28" width="30" height="32" rx="3" fill="none" stroke="#6d6d6d" stroke-width="2.5"/>
      <g fill="#6d6d6d"><rect x="35" y="45" width="4" height="10"/><rect x="42" y="39" width="4" height="16"/><rect x="49" y="33" width="4" height="22"/></g>
    </svg>
    <h4>Quality over Quantity</h4>
    <p>Proin iaculis purus consequat sem cure digni ssim. Donec porttitora entum suscipit aenean rhoncus posuere nibh in tincidunt.</p>
  </div>
  <div class="card abs" style="left:748px;top:234px">
    <svg class="ring-icon" viewBox="0 0 88 88" aria-hidden="true">
      <circle cx="44" cy="44" r="41" fill="#fff" stroke="#6d6d6d" stroke-width="5"/>
      <rect x="28" y="28" width="32" height="32" rx="3" fill="none" stroke="#6d6d6d" stroke-width="2.5"/>
      <polyline points="32,53 39,44 45,48 55,35" fill="none" stroke="#6d6d6d" stroke-width="3"/>
    </svg>
    <h4>Deliver Excellence</h4>
    <p>Proin iaculis purus consequat sem cure digni ssim. Donec porttitora entum suscipit aenean rhoncus posuere nibh in tincidunt.</p>
  </div>
</section>

<section class="call">
  <svg class="call-badge abs" viewBox="0 0 90 90" aria-hidden="true">
    <circle cx="45" cy="45" r="45" fill="#1aa3ee"/>
    <path d="M36 30c2-2 4-1 5 1l3 6c1 2 0 3-1 4l-2 2c2 4 5 7 9 9l2-2c1-1 2-2 4-1l6 3c2 1 3 3 1 5l-3 3c-3 3-9 1-16-6s-9-13-6-16z" fill="#fff"/>
  </svg>
  <p class="call-label abs center">CALL</p>
  <p class="call-number abs center">02 9000 4821</p>
</section>

<section class="contact">
  <div class="contact-photo" role="img" aria-label="Photo of a pen resting on printed financial charts in soft blue tones"></div>
  <h2 class="section-title abs center">Contact Us</h2>
  <p class="section-sub abs center">Lorem ipsum dolor sit amet</p>
  <div class="field field-name abs"></div>
  <div class="field field-email abs"></div>
  <div class="field field-message abs"></div>
  <div class="send-button abs">SEND</div>
</section>

<footer class="site-footer">
  <div class="wordmark footer-logo abs">Brook &amp; Associates</div>
  <span class="social abs" style="left:954px" aria-label="Social link"></span>
  <span class="social abs" style="left:1009px" aria-label="Social link"></span>
</footer>

</body>
</html>
```